Marlowe Group needs a business card

I would like the card to be simple but modern and elegant.
I like black and white.
or black and gold.
we are a private finance lender and also are involved in property and property developments.

please look at the business card photos i provided i would like M.G only one one side and all the other details on the other side use fonts that tie in with my theme.

Industry/Entity Type

Finance

Contact Information for Business Card

Marlowe Group (M.G) Daniel Marlowe M: 0413586207 E: danmarl@inboxmail.test

Font styles to use
Other font styles liked:
• Use fonts that would reflect our business

Colors
000000
ffffff

Requirements
Must have
• one side of details
• other side has either M.G or Marlowe Group like in the photos provided

```html
<!DOCTYPE html>
<html lang="en">
<head>
<meta charset="utf-8">
<title>Marlowe Group — Business Card</title>
<link rel="stylesheet" href="https://fonts.googleapis.com/css2?family=Saira:wght@400;600&family=Montserrat:wght@300;400&display=swap">
<style>
  :root {
    --stage: #2a2a2a;
    --card: #000000;
    --ink: #ffffff;
    --ink-soft: #e6e6e6;
  }
  * { margin: 0; padding: 0; box-sizing: border-box; }
  html, body {
    width: 1200px;
    height: 900px;
    overflow: hidden;
    background: var(--stage);
  }
  .stage {
    width: 1200px;
    height: 900px;
    display: flex;
    flex-direction: column;
    align-items: center;
    justify-content: center;
    gap: 48px;
  }
  .card {
    width: 560px;
    height: 320px;
    background: var(--card);
    position: relative;
    box-shadow: 0 14px 34px rgba(0, 0, 0, 0.55);
  }
  .card-front {
    display: flex;
    align-items: center;
    justify-content: center;
  }
  .brand-mark {
    font-family: "Saira", sans-serif;
    font-weight: 600;
    font-size: 64px;
    letter-spacing: 4px;
    color: var(--ink);
  }
  .card-back .details {
    position: absolute;
    left: 70px;
    top: 168px;
    display: flex;
    align-items: center;
  }
  .holder-name {
    font-family: "Saira", sans-serif;
    font-weight: 600;
    font-size: 17px;
    letter-spacing: 1.2px;
    text-transform: uppercase;
    color: var(--ink);
    padding-right: 14px;
  }
  .divider {
    width: 1.5px;
    height: 40px;
    background: var(--ink);
  }
  .contact-list {
    list-style: none;
    padding-left: 12px;
    font-family: "Montserrat", sans-serif;
    font-weight: 400;
    font-size: 12.5px;
    line-height: 19px;
    letter-spacing: 0.8px;
    color: var(--ink-soft);
  }
  .contact-list .label { margin-right: 6px; }
</style>
</head>
<body>
  <main class="stage">
    <section class="card card-front" aria-label="Card front">
      <span class="brand-mark">M.G</span>
    </section>
    <section class="card card-back" aria-label="Card back">
      <div class="details">
        <h1 class="holder-name">Daniel Marlowe</h1>
        <span class="divider" aria-hidden="true"></span>
        <ul class="contact-list">
          <li><span class="label">M:</span>041. 358. 6207</li>
          <li><span class="label">E:</span>danmarl@inboxmail.test</li>
        </ul>
      </div>
    </section>
  </main>
</body>
</html>
```